Brightlane Rapid Rinse Web Design

We are looking for a web design that highlights our state of the art fully automated commercial vehicle washing equipment. Similar system to a car wash however this system is meant for the largest vehicles on our roadways. Transport trucks with or without a trailer, busses both highway and school, RV's from 5th wheel type to A Class. Cement trucks, dump trucks, vac trucks, fuel trucks etc. Pick ups with utility trailers...Refrigerator truck clean outs.
Brightlane Rapid Rinse will wash your vehicle quickly and with a minimal impact on the environment

Home page
About us
Why Brightlane
Services and pricing
Videos of wash system
Fleets
contact us

Target Market(s)

Commercial vehicle owners and operators as well as corporate fleets. Includes busses, municipal, school and highway.both school and

Industry/Entity Type

transportation

Coding

Coded - Design and coding required

Number of Pages Required

5+ page

Font styles to use
Sans Serif

Colors
0054AA
0677BA
7BADD7
CADEEF
E8F1F8

Requirements
Must have
• Welcome page,why us page which describes the financial and environmental benefits. payment processing page, contact us page, Services which is washing vehicles and greasing for commercial vehicles that want that service and grease
Nice to have
• pictures of both clean and dirty commercial vehicles ie. before and after

```html
<!DOCTYPE html>
<html lang="en">
<head>
<meta charset="utf-8">
<title>Brightlane Rapid Rinse</title>
<link href="https://fonts.googleapis.com/css2?family=Montserrat:wght@400;500;600;700&display=swap" rel="stylesheet">
<style>
:root{
  --blue:#0054AA;
  --blue-mid:#0677BA;
  --blue-soft:#7BADD7;
  --blue-pale:#CADEEF;
  --blue-mist:#E8F1F8;
  --ink:#1d1d1f;
  --white:#ffffff;
  --ghost:#eef1f5;
}
*{margin:0;padding:0;box-sizing:border-box}
html,body{width:1200px;height:4160px;overflow:hidden;background:var(--white)}
body{position:relative;font-family:'Montserrat',sans-serif;color:var(--ink)}
.abs{position:absolute}
.btn{position:absolute;display:flex;align-items:center;justify-content:center;background:var(--blue);color:var(--white);border-radius:32px;font-weight:500;font-size:20px;letter-spacing:.2px;white-space:nowrap}
.photo{position:absolute}
.vline{position:absolute;width:2px;background:var(--blue)}
.heading{position:absolute;color:var(--blue);font-weight:600;font-size:32px;letter-spacing:.8px}
.body-text{position:absolute;font-size:15.5px;line-height:36px;color:var(--ink)}
.ghost{position:absolute;font-weight:700;font-size:76px;color:var(--ghost);letter-spacing:2px;line-height:1}

/* header */
.site-header{position:absolute;left:0;top:0;width:1200px;height:86px;background:var(--blue)}
.brand{position:absolute;left:71px;top:6px;width:260px;color:var(--white);font-weight:600;font-size:19.5px;line-height:37px;letter-spacing:.3px}
.nav{position:absolute;left:400px;top:34px;display:flex;gap:26px;color:var(--white);font-weight:600;font-size:12.5px;white-space:nowrap}
.nav-divider{position:absolute;left:1076px;top:22px;width:2px;height:42px;background:var(--blue-soft)}

/* hero */
.hero{left:0;top:86px;width:1200px;height:578px;background:linear-gradient(90deg,#050505 0%,#0c0c0c 42%,#3b4046 62%,#8f9aa2 72%,#6d7479 85%,#1f5c50 100%)}
.hero-title{position:absolute;left:81px;top:232px;font-size:49px;font-weight:500;line-height:76px;color:var(--white);letter-spacing:.5px}
.hero-title span{color:var(--blue-soft);font-weight:600}
.scroll{position:absolute;left:540px;top:606px;width:120px;text-align:center;color:var(--white);font-size:13px;font-weight:600}
.social-rail{position:absolute;left:1121px;top:287px;width:55px;height:328px;background:var(--blue);border-radius:28px}

/* services */
.svc-title{position:absolute;color:var(--blue);font-weight:600;font-size:17px;letter-spacing:.3px;white-space:nowrap}

/* pricing */
.price-row{position:absolute;left:604px;width:434px;height:54px;border-bottom:1.5px solid var(--blue);font-size:15px;font-weight:500;white-space:nowrap}
.price-row span{position:absolute;top:6px;white-space:nowrap}
.price-row .tier{left:199px;color:var(--blue);font-weight:600}
.price-row .amt{left:394px}

/* before/after */
.tag{position:absolute;width:65px;height:226px;background:var(--blue);border-radius:33px}
.tag-label{position:absolute;left:50%;top:26px;transform:translateX(-50%);writing-mode:vertical-rl;rotate:180deg;color:var(--white);font-weight:600;font-size:16px;letter-spacing:1px}
.tag-line{position:absolute;left:31px;top:122px;width:2px;height:90px;background:var(--white)}

/* blog */
.post-title{position:absolute;font-weight:500;font-size:17.5px;line-height:36px;letter-spacing:.4px;white-space:nowrap}

/* footer */
.site-footer{position:absolute;left:0;top:3803px;width:1200px;height:357px;background:var(--blue);color:var(--white)}
.f-brand{position:absolute;left:102px;top:94px;width:320px;font-size:22px;font-weight:600;line-height:45px}
.f-contact{position:absolute;left:510px;font-size:16px;font-weight:500;display:flex;align-items:center;gap:22px;white-space:nowrap}
.f-social{position:absolute;top:122px;width:28px;height:28px;border:2.5px solid var(--white);border-radius:50%}
.copyright{position:absolute;left:0;top:297px;width:1200px;text-align:center;font-size:16px;font-weight:600}
</style>
</head>
<body>

<header class="site-header">
  <div class="brand">BRIGHTLANE RAPID RINSE</div>
  <nav class="nav">
    <span>HOME</span><span>ABOUT US</span><span>WHY BRIGHTLANE</span><span>SERVICES</span><span>VIDEOS</span><span>FLEETS</span><span>CONTACT US</span>
  </nav>
  <div class="nav-divider"></div>
  <svg class="abs" style="left:1111px;top:33px" width="18" height="18" viewBox="0 0 18 18" fill="none" stroke="#fff" stroke-width="1.6"><circle cx="7.5" cy="7.5" r="5.5"/><path d="M11.5 11.5L16 16"/></svg>
</header>

<section>
  <div class="photo hero" role="img" aria-label="White semi truck cab inside an automated wash bay with green brushes and water spray"></div>
  <h1 class="hero-title">SPEED IS LESS THAN<br><span>15 MINUTES</span></h1>
  <div class="btn" style="left:81px;top:410px;width:221px;height:62px">BOOK A WASH</div>
  <div class="btn" style="left:315px;top:410px;width:187px;height:62px">CONTACT US</div>
  <div class="btn" style="left:514px;top:410px;width:187px;height:62px">LEARN MORE</div>
  <svg class="abs" style="left:98px;top:608px" width="40" height="22" viewBox="0 0 40 22" fill="none" stroke="#fff" stroke-width="2"><path d="M38 11H3M11 3L3 11l8 8"/></svg>
  <svg class="abs" style="left:192px;top:608px" width="40" height="22" viewBox="0 0 40 22" fill="none" stroke="#fff" stroke-width="2"><path d="M2 11h35M29 3l8 8-8 8"/></svg>
  <div class="scroll">SCROLL DOWN
    <svg style="display:block;margin:6px auto 0" width="14" height="9" viewBox="0 0 14 9" fill="none" stroke="#fff" stroke-width="1.6"><path d="M1 1l6 6 6-6"/></svg>
  </div>
  <div class="social-rail">
    <div class="abs" style="left:26px;top:26px;width:2px;height:72px;background:#fff"></div>
    <div class="abs" style="left:21px;top:140px;width:12px;height:12px;background:#fff;border-radius:50%"></div>
    <div class="abs" style="left:21px;top:187px;width:12px;height:12px;background:#fff;border-radius:50%"></div>
    <div class="abs" style="left:21px;top:234px;width:12px;height:12px;background:#fff;border-radius:50%"></div>
    <div class="abs" style="left:21px;top:280px;width:12px;height:12px;background:#fff;border-radius:50%"></div>
  </div>
</section>

<section>
  <div class="vline" style="left:110px;top:685px;height:61px"></div>
  <div class="photo" style="left:0;top:757px;width:685px;height:391px;background:linear-gradient(90deg,#c9cfd3 0%,#1e6b58 10%,#9ba3a8 25%,#e5e8ea 50%,#9aa1a6 75%,#1e6b58 90%,#c6ccd0 100%)" role="img" aria-label="Front view of a white truck cab passing through wash brushes"></div>
  <h2 class="heading" style="left:740px;top:762px">ABOUT US</h2>
  <p class="body-text" style="left:740px;top:823px;width:360px">Lorem ipsum dolor sit amet, consectetur adipiscing elit, sed do eiusmod tempor incididunt ut labore et dolore magna aliqua. Ut enim ad minim veniam, quis nostrud exercitation ullamco laboris nisi ut aliquip ex ea commodo consequat.</p>
  <div class="btn" style="left:740px;top:1067px;width:187px;height:62px">OUR MISSION</div>
</section>

<section>
  <h2 class="heading" style="left:0;top:1236px;width:1200px;text-align:center">OUR SERVICES</h2>
  <div class="ghost" style="left:0;top:1290px">SERVICES</div>
  <div class="photo" style="left:0;top:1340px;width:400px;height:458px;background:linear-gradient(180deg,#2d5f93 0%,#6f9fd0 35%,#1b2c44 65%,#a84a2a 100%)" role="img" aria-label="Car in a blue lit automatic wash tunnel with water spray"></div>
  <div class="photo" style="left:400px;top:1340px;width:400px;height:458px;background:linear-gradient(160deg,#1a1c1f 0%,#3d3a35 45%,#7a5a2a 60%,#24272b 100%)" role="img" aria-label="Oil pouring into an engine filler for lubrication service"></div>
  <div class="photo" style="left:800px;top:1340px;width:400px;height:458px;background:linear-gradient(150deg,#4f7f90 0%,#8fb0bb 40%,#c9d5da 70%,#e7ecee 100%)" role="img" aria-label="Hand holding a tablet with fleet dashboard beside parked trucks"></div>
  <div class="vline" style="left:32px;top:1744px;height:81px"></div>
  <div class="vline" style="left:432px;top:1744px;height:81px"></div>
  <div class="vline" style="left:832px;top:1744px;height:81px"></div>
  <h3 class="svc-title" style="left:32px;top:1842px">AUTOMATED TRUCK WASH</h3>
  <h3 class="svc-title" style="left:432px;top:1842px">ADDITIONAL SERVICES</h3>
  <h3 class="svc-title" style="left:831px;top:1842px">FLEET SERVICES</h3>
  <p class="body-text" style="left:32px;top:1881px;width:340px">Lorem ipsum dolor sit amet, consectetur adipiscing elit, sed do</p>
  <p class="body-text" style="left:432px;top:1881px;width:340px">Lorem ipsum dolor sit amet, consectetur adipiscing elit, sed do</p>
  <p class="body-text" style="left:832px;top:1881px;width:340px">Lorem ipsum dolor sit amet, consectetur adipiscing elit, sed do</p>
  <div class="btn" style="left:489px;top:1982px;width:222px;height:62px">VIEW SERVICES</div>
</section>

<section>
  <div class="ghost" style="left:0;top:2130px">PRICING</div>
  <h2 class="heading" style="left:160px;top:2146px">OUR PRICING</h2>
  <p class="body-text" style="left:160px;top:2209px;width:330px">Lorem ipsum dolor sit amet, consectetur adipiscing elit, sed do eiusmod tempor incididunt ut labore</p>
  <div class="btn" style="left:160px;top:2343px;width:187px;height:62px">VIEW PRICING</div>
  <div class="abs" style="left:0;top:2127px">
    <div class="price-row" style="top:0"><span>12:00 - 09:30 PM</span><span class="tier">BASIC WASH</span><span class="amt">$ 45</span></div>
    <div class="price-row" style="top:54px"><span>12:00 - 09:30 PM</span><span class="tier">STANDARD</span><span class="amt">$ 80</span></div>
    <div class="price-row" style="top:108px"><span>12:00 - 09:30 PM</span><span class="tier">STANDARD PLUS</span><span class="amt">$ 120</span></div>
    <div class="price-row" style="top:162px"><span>12:00 - 09:30 PM</span><span class="tier">PREMIUM</span><span class="amt">$ 459</span></div>
    <div class="price-row" style="top:216px"><span>12:00 - 09:30 PM</span><span class="tier">POLYMER PRO</span><span class="amt">$ 90</span></div>
    <div class="price-row" style="top:270px;border-bottom:none"><span>12:00 - 09:30 PM</span><span class="tier">WASH AND WAX</span><span class="amt">$ 461</span></div>
  </div>
</section>

<section>
  <div class="photo" style="left:0;top:2511px;width:712px;height:464px;background:linear-gradient(180deg,#6f9ed0 0%,#a9c6e2 30%,#8a7a5e 55%,#5c4a35 100%)" role="img" aria-label="Mud covered white truck driving through a muddy field, before washing"></div>
  <div class="tag" style="left:13px;top:2539px"><span class="tag-label">BEFORE</span><span class="tag-line"></span></div>
  <p class="body-text" style="left:48px;top:2997px;width:660px;font-size:15px">Lorem ipsum dolor sit amet, consectetur adipiscing elit, sed do eiusmod tempor incididunt ut labore &nbsp;et dolore magna aliqua. Ut enim ad minim veniam, quis nostrud exercitation ullamco laboris nisi ut aliquip ex ea</p>
  <div class="btn" style="left:48px;top:3131px;width:188px;height:62px">VIEW MORE</div>
  <div class="photo" style="left:740px;top:2511px;width:460px;height:708px;background:linear-gradient(170deg,#1b2433 0%,#2b5f80 40%,#3f8fb5 55%,#12202d 100%)" role="img" aria-label="Clean blue dump truck on a wet street at night, after washing"></div>
  <div class="tag" style="left:756px;top:2539px"><span class="tag-label">AFTER</span><span class="tag-line"></span></div>
</section>

<section>
  <div class="photo" style="left:110px;top:3316px;width:421px;height:279px;background:linear-gradient(180deg,#5f8a5a 0%,#9aa48a 40%,#d8832a 65%,#6c6b66 100%)" role="img" aria-label="Orange garbage truck parked on a city street"></div>
  <div class="photo" style="left:559px;top:3316px;width:421px;height:279px;background:linear-gradient(180deg,#5e8fc9 0%,#a8c4e2 40%,#a8402f 60%,#4d4d52 100%)" role="img" aria-label="White truck hauling a red shipping container at sunset"></div>
  <div class="photo" style="left:1006px;top:3316px;width:194px;height:279px;background:linear-gradient(90deg,#d5d9dc 0%,#9aa2a8 50%,#3c4045 100%)" role="img" aria-label="Close view of a white truck cab front"></div>
  <div class="vline" style="left:142px;top:3595px;height:39px"></div>
  <div class="vline" style="left:591px;top:3595px;height:39px"></div>
  <div class="vline" style="left:1039px;top:3595px;height:39px"></div>
  <h3 class="post-title" style="left:110px;top:3646px">LOREM IPSUM DOLOR SIT AMET,<br>CONSECTETUR</h3>
  <h3 class="post-title" style="left:559px;top:3646px">LOREM IPSUM DOLOR SIT AMET,<br>CONSECTETUR</h3>
  <h3 class="post-title" style="left:1006px;top:3646px">LOREM IPSUM DOLOR SIT AMET,<br>CONSECTETUR</h3>
  <div class="ghost" style="left:0;top:3743px">BLOG</div>
</section>

<footer class="site-footer">
  <div class="f-brand">BRIGHTLANE RAPID<br>RINSE</div>
  <div class="f-contact" style="top:67px">
    <svg width="16" height="16" viewBox="0 0 16 16" fill="none" stroke="#fff" stroke-width="1.5"><path d="M3 1.5l3 3-1.5 2a8 8 0 0 0 5 5l2-1.5 3 3-2 2C7 14.5 1.5 9 1 3z"/></svg>
    <span>+1 555 014 2290</span></div>
  <div class="f-contact" style="top:119px">
    <svg width="16" height="14" viewBox="0 0 16 14" fill="none" stroke="#fff" stroke-width="1.5"><rect x="1" y="1.5" width="14" height="11" rx="1"/><path d="M1 2l7 6 7-6"/></svg>
    <span>INFO@BRIGHTLANERINSE.COM</span></div>
  <div class="f-contact" style="top:171px;gap:14px">
    <svg width="16" height="18" viewBox="0 0 16 18" fill="none" stroke="#fff" stroke-width="1.5"><path d="M8 17s6-6 6-10A6 6 0 0 0 2 7c0 4 6 10 6 10z"/><circle cx="8" cy="7" r="2"/></svg>
    <span>410 HARBOR LINE RD, UNIT 12</span></div>
  <div class="f-social" style="left:902px"></div>
  <div class="f-social" style="left:958px"></div>
  <div class="f-social" style="left:1015px"></div>
  <div class="f-social" style="left:1071px"></div>
  <div class="copyright">@2024 COPYRIGHTS &nbsp;PRIVACY POLICY</div>
</footer>

</body>
</html>
```